Re-Design of a 1 Pager IT Security Website

Please create a 1 Pager design for this website and all its elements: http://www.quillstonebrightmarsh.com/

Colours, Fonts etc: You can select whatever you prefer

```html
<!DOCTYPE html>
<html lang="en">
<head>
<meta charset="utf-8">
<title>Domain Monitoring – Veltrani</title>
<link rel="stylesheet" href="https://fonts.googleapis.com/css2?family=Oswald:wght@300;400;500;600&display=swap">
<style>
:root{
  --bg:#000000;
  --ink:#ffffff;
  --muted:#d5d8e4;
  --blue:#1e5fc4;
  --blue-bright:#2b74e0;
  --purple:#3a1896;
  --line:#1f5fb8;
  --card-border:#2a2a2e;
  --frame:#4a4a4e;
  --play:#2a2d3a;
}
*{box-sizing:border-box;margin:0;padding:0}
html,body{width:1200px;height:5038px;overflow:hidden;background:var(--bg)}
body{position:relative;font-family:'Oswald',sans-serif;color:var(--ink)}
.abs{position:absolute}
.texture{position:absolute;left:0;width:1200px;background:
  radial-gradient(ellipse at 50% 50%,rgba(60,80,130,.22),rgba(0,0,0,0) 65%);}
.logo{left:143px;top:44px;font-size:38px;font-weight:500;letter-spacing:-.5px}
.burger{left:1027px;top:54px;width:28px}
.burger span{display:block;height:4px;background:var(--ink);margin-bottom:6px;border-radius:1px}
.hero-title{left:140px;top:166px;font-size:58px;line-height:68px;font-weight:500;text-transform:uppercase;letter-spacing:-.5px}
.hero-title .hl{color:var(--blue)}
.btn{display:flex;align-items:center;justify-content:center;border-radius:32px;
  background:linear-gradient(90deg,var(--purple),var(--blue-bright));font-weight:500;font-size:17px;text-transform:uppercase}
.hero-btn{left:140px;top:419px;width:210px;height:58px}
.hero-media{left:600px;top:128px;width:600px;height:367px;border-radius:200px 0 0 200px;
  background:linear-gradient(135deg,#1b2b55,#0a1020 55%,#2b3f7a);box-shadow:-10px 0 0 0 #3a1aa0}
.dots{left:143px;top:612px;display:flex;gap:12px}
.dots i{width:6px;height:6px;border-radius:50%;background:#fff;display:block}
.dots i:nth-child(2){background:#9aa}
.divider{position:absolute;width:2px;background:var(--line)}
.divider::before{content:"";position:absolute;left:-4px;top:-4px;width:10px;height:10px;border-radius:50%;background:var(--line)}
.heading{position:absolute;font-weight:500;font-size:48px;text-transform:uppercase;letter-spacing:-.5px;line-height:1}
.center{left:0;width:1200px;text-align:center}
.body-text{position:absolute;font-weight:300;font-size:15.5px;line-height:29px;color:var(--muted)}
.video{left:145px;top:853px;width:910px;height:495px;border:6px solid var(--frame);
  background:linear-gradient(120deg,#f4f4f6 0%,#ececf0 50%,#d9d8e2 100%)}
.play{left:576px;top:1078px}
.card{position:absolute;top:1785px;width:288px;height:415px;border:2px solid var(--card-border);border-radius:10px;padding:0 20px;text-align:center}
.card.active{background:linear-gradient(180deg,var(--blue) 0%,var(--purple) 100%);border-color:transparent}
.card svg{margin-top:25px}
.card h3{font-weight:500;font-size:19px;margin-top:12px}
.card p{font-weight:300;font-size:11.2px;line-height:20px;color:var(--muted);margin-top:12px;text-align:justify;text-align-last:center}
.protect-art{left:705px;top:2440px;width:420px;height:300px;border-radius:12px;
  background:radial-gradient(ellipse at 50% 55%,#2f6ad8,#1a3f9e 45%,rgba(0,0,0,0) 72%)}
.link{color:var(--blue-bright);text-decoration:underline}
.band{left:0;top:2845px;width:1200px;height:540px;background:linear-gradient(110deg,#15275a,#243f8c 35%,#2d3a86 60%,#4b3d98)}
.band-cut{left:143px;top:3335px;width:912px;height:60px;background:var(--bg)}
.checks{left:168px;top:3717px;width:890px;display:grid;grid-template-columns:458px 432px;row-gap:18px;font-weight:500;font-size:17px}
.checks li{list-style:none;display:flex;align-items:center;gap:12px}
.about-art{left:650px;top:3890px;width:410px;height:410px;border-radius:50%;
  background:radial-gradient(circle at 50% 55%,#2b4b8e,#14203e 60%,#0b1124);box-shadow:-14px -6px 0 0 #3a1aa0}
.field{position:absolute;background:#fff;color:#555;font-weight:300;font-size:15px;padding:18px 20px}
.footer{left:143px;top:4972px;font-weight:300;font-size:11px;color:var(--muted)}
.social{position:absolute;top:4968px;width:26px;height:26px;border-radius:50%;background:#fff}
</style>
</head>
<body>

<div class="texture" style="top:560px;height:260px"></div>
<div class="texture" style="top:2230px;height:200px"></div>
<div class="texture" style="top:3850px;height:220px"></div>
<div class="texture" style="top:4780px;height:220px"></div>

<header>
  <div class="abs logo">DOMAIN MONITORING</div>
  <div class="abs burger" aria-label="Menu"><span></span><span></span><span></span></div>
</header>

<section class="hero">
  <h1 class="abs hero-title"><span class="hl">Prevent attacks</span><br>by monitoring<br><span class="hl">your domains</span></h1>
  <a class="abs btn hero-btn">Learn more</a>
  <div class="abs hero-media" role="img" aria-label="Photo of hands on a laptop with floating padlock screens"></div>
  <div class="abs dots"><i></i><i></i><i></i></div>
</section>

<section class="explainer">
  <div class="divider" style="left:599px;top:645px;height:90px"></div>
  <h2 class="heading center" style="top:748px">Domain monitoring explainer</h2>
  <div class="abs video" role="img" aria-label="Video still of connected computer monitors"></div>
  <svg class="abs play" width="48" height="48" viewBox="0 0 48 48" aria-label="Play video"><circle cx="24" cy="24" r="24" fill="var(--play)"/><path d="M19 14 L34 24 L19 34Z" fill="#fff"/></svg>
</section>

<section class="risk">
  <div class="divider" style="left:599px;top:1410px;height:90px"></div>
  <h2 class="heading center" style="top:1514px">What is the risk?</h2>
  <p class="body-text" style="left:188px;top:1600px;width:824px;text-align:justify">Hackers use domain-based attacks, which are designed to trick users into submitting sensitive data or downloading dangerous files. This is often the case with phishing attacks. For example, domains can be registered that are very similar to one's own company, a customer or a supplier. Once a fraudulent domain is registered, the hackers try to lure the employee to the website. This can be done via e-mail, SMS (smishing), instant messaging. Social media and many other techniques succeed. A distinction is made between different types of attacks:</p>

  <div class="card" style="left:143px">
    <svg width="86" height="78" viewBox="0 0 86 78"><rect x="3" y="3" width="80" height="54" rx="5" fill="none" stroke="#2b74e0" stroke-width="7"/><rect x="36" y="58" width="14" height="12" fill="#2b74e0"/><rect x="22" y="70" width="42" height="6" rx="2" fill="#2b74e0"/></svg>
    <h3>Domain spoofing</h3>
    <p>Here, a domain name is registered that resembles that of a trusted brand or organization. For example, the hacker can register the domain "paybridge-access.services" and lure the victim to the website under a certain pretext. At the same time, the original website can also be copied 1:1, so that visually there is no difference.</p>
  </div>
  <div class="card active" style="left:455px">
    <svg width="96" height="84" viewBox="0 0 96 84"><path d="M48 4 L92 80 H4Z" fill="#fff" stroke="#fff" stroke-width="6" stroke-linejoin="round"/><rect x="44" y="28" width="8" height="30" rx="3" fill="#2450c0"/><circle cx="48" cy="67" r="5" fill="#2450c0"/></svg>
    <h3>Homoglyphic Attack</h3>
    <p>This is a variant of domain spoofing. Again, a similar looking domain is registered. But one uses characters outside the Latin alphabet in the domain name that resemble the corresponding characters in the URL of the target domain. Replacing the "g" with q is also very popular. Multi-letter homoglyphs are also popular, e.g. "rn" instead of "m". In more complex scenarios, homoglyphs can also be generated with the use of different alphabets and special characters.</p>
  </div>
  <div class="card" style="left:767px">
    <svg width="84" height="84" viewBox="0 0 84 84"><path d="M10 62 L56 16 L68 28 L22 74 L6 78Z" fill="#2b74e0"/><path d="M60 12 L66 6 Q70 2 74 6 L78 10 Q82 14 78 18 L72 24Z" fill="#2b74e0"/></svg>
    <h3>Typosquatting</h3>
    <p>cybercriminals may attempt to register a malicious domain by using a common misspelling of the target company's domain. For example, someone might reserve "paybrldge.com" because the letter "L" and "K" are next to each other at the keyboard. If a customer of the target company misspells the domain, he will land on the fraudulent domain where he can become a victim of cybercriminals.</p>
  </div>
</section>

<section class="protect">
  <div class="divider" style="left:153px;top:2393px;height:90px"></div>
  <h2 class="heading" style="left:147px;top:2500px">How to protect yourself?</h2>
  <p class="body-text" style="left:148px;top:2575px;width:480px">Our domain monitoring solution continuously monitors thousands of TLDs, gTLDs and ccTLDs. For searches, we offer the greatest flexibility in the market and cover ALL forms of attacks. Here are a few examples of search options that can be adopted as active alerts:<br>&nbsp;<span class="link">https://wiki.veltrani.example/docs/domain-search</span><br>All data can be analyzed and exported.</p>
  <div class="abs protect-art" role="img" aria-label="Illustration of people around a laptop with a secure https shield"></div>
</section>

<div class="abs band" role="img" aria-label="Photo of a digital globe and network lines over a laptop keyboard"></div>
<div class="abs band-cut"></div>

<section class="monitoring">
  <div class="divider" style="left:599px;top:3378px;height:90px"></div>
  <h2 class="heading center" style="top:3484px">What else are we monitoring?</h2>
  <p class="body-text" style="left:205px;top:3555px;width:790px;text-align:center">Veltrani helps you understand when, where and how stolen or accidentally leaked information in dark web markets, forums, botnet logs, IRC, social media and other sources is exposed. Veltrani's alerting service can also detect threats before they turn into incidents. Veltrani offers AI-driven dark web analysis, real-time threat alerts and pre-Attack threat indicators. Setup in minutes you will receive instant access to real-time reporting including:</p>
  <ul class="abs checks">
    <li><svg width="16" height="14"><path d="M2 7 L6 11 L14 2" fill="none" stroke="#2b74e0" stroke-width="3"/></svg>Infrastructure exposure: IOT, code repos, cloud &amp; more</li>
    <li><svg width="16" height="14"><path d="M2 7 L6 11 L14 2" fill="none" stroke="#2b74e0" stroke-width="3"/></svg>People exposure: Social media monitoring</li>
    <li><svg width="16" height="14"><path d="M2 7 L6 11 L14 2" fill="none" stroke="#2b74e0" stroke-width="3"/></svg>Ransomware exposure: leak &amp; credential monitoring</li>
    <li><svg width="16" height="14"><path d="M2 7 L6 11 L14 2" fill="none" stroke="#2b74e0" stroke-width="3"/></svg>Attack prevention: domain and certificate monitoring</li>
  </ul>
</section>

<section class="about">
  <div class="divider" style="left:147px;top:3918px;height:90px"></div>
  <h2 class="heading" style="left:143px;top:4010px">About Veltrani</h2>
  <p class="body-text" style="left:143px;top:4100px;width:480px">Veltrani (company registration number CHE-481.207.593) was started in 2018 as a public limited company in Zug, Switzerland. Our analysts have long-standing relationships with various players on the Darknet. These personal relationships make it possible for Veltrani to repeatedly obtain the latest data leaks. Those unique data leaks are published by the press around the world.</p>
  <div class="abs about-art" role="img" aria-label="Photo of hands on a keyboard with a glowing warning sign"></div>
</section>

<section class="contact">
  <div class="divider" style="left:599px;top:4400px;height:85px"></div>
  <h2 class="heading center" style="top:4510px">Want to know more?</h2>
  <div class="field" style="left:268px;top:4622px;width:325px;height:53px">Your Name</div>
  <div class="field" style="left:268px;top:4692px;width:325px;height:53px">Your Email</div>
  <div class="field" style="left:607px;top:4622px;width:325px;height:123px">Message</div>
  <a class="abs btn" style="left:495px;top:4795px;width:208px;height:60px">Submit</a>
</section>

<footer>
  <div class="abs footer">© Veltrani.example · All rights reserved &nbsp;|&nbsp; Privacy &nbsp;|&nbsp; Terms and Conditions</div>
  <div class="social" style="left:970px" aria-label="Chirpline"></div>
  <div class="social" style="left:1028px;border-radius:4px" aria-label="Workmesh"></div>
</footer>

</body>
</html>
```